Realty Group Needs Classy, Contemporary Letterhead Design

We need a letterhead design for a new realty company located in NY, USA. We buy investment properties to rehabilitate and or keep in our rental portfolio.

```html
<!DOCTYPE html>
<html lang="en">
<head>
<meta charset="UTF-8">
<title>Meridian Realty Group — Letterhead</title>
<link rel="stylesheet" href="https://fonts.googleapis.com/css2?family=Open+Sans:wght@400;600;700&family=Dancing+Script&display=swap">
<style>
  :root {
    --backdrop: #c9c9c9;
    --paper: #ffffff;
    --brand-purple: #4f2a8c;
    --accent-grey: #8c8c8c;
    --text-grey: #6f6f6f;
    --text-dark: #4a4a4a;
  }
  * { box-sizing: border-box; margin: 0; padding: 0; }
  html, body { width: 1200px; height: 795px; overflow: hidden; }
  body {
    background: var(--backdrop);
    font-family: "Open Sans", sans-serif;
    display: flex; align-items: center; justify-content: center;
  }
  .letterhead {
    position: relative;
    width: 523px; height: 740px;
    background: var(--paper);
    box-shadow: 0 6px 18px rgba(0,0,0,.18);
    overflow: hidden;
    color: var(--text-grey);
  }
  .header-shapes { position: absolute; top: 0; left: 0; width: 523px; height: 140px; }
  .brand {
    position: absolute; top: 126px; left: 34px;
    display: flex; align-items: center; gap: 6px;
    color: var(--brand-purple); font-weight: 700; font-size: 15px; letter-spacing: .3px;
  }
  .brand-mark { width: 10px; height: 10px; background: var(--brand-purple); }
  .letter {
    position: absolute; top: 185px; left: 60px; right: 60px;
    font-size: 7.6px; line-height: 1.5;
  }
  .date { margin-bottom: 12px; }
  .recipient { margin-bottom: 12px; }
  .salutation { font-weight: 700; color: var(--text-dark); margin-bottom: 12px; }
  .letter p { margin-bottom: 12px; text-align: justify; }
  .signoff { margin-top: 22px; }
  .signature {
    font-family: "Dancing Script", cursive;
    font-size: 24px; color: var(--text-dark); line-height: 1.2; margin: 2px 0 2px 14px;
  }
  .signer { margin-left: 30px; }
  .footer-details {
    position: absolute; right: 28px; bottom: 32px;
    text-align: right; font-size: 7px; line-height: 1.5; color: var(--text-dark);
  }
  .footer-details .company { color: var(--brand-purple); font-weight: 700; font-size: 8px; }
  .contact-bar {
    position: absolute; left: 0; right: 0; bottom: 0; height: 22px;
    background: var(--brand-purple);
    display: flex; align-items: center; justify-content: flex-end; gap: 10px;
    padding-right: 28px; color: #fff; font-size: 7px; font-weight: 600;
  }
  .contact-item { display: flex; align-items: center; gap: 3px; }
  .contact-item svg { width: 8px; height: 8px; fill: #fff; }
</style>
</head>
<body>
<main class="letterhead">
  <svg class="header-shapes" viewBox="0 0 523 140" aria-hidden="true">
    <polygon points="0,40 0,132 52,112" fill="var(--accent-grey)"/>
    <polygon points="250,0 523,0 523,30 52,112" fill="var(--brand-purple)"/>
    <polygon points="523,36 523,42 64,116 58,115" fill="var(--accent-grey)"/>
  </svg>

  <div class="brand"><span class="brand-mark"></span>Meridian Realty Group</div>

  <section class="letter">
    <div class="date">January 12, 2014</div>
    <div class="recipient">Mr. John Doe<br>President<br>AA Corporation<br>111 Street Name, Suite#<br>City, State, 12345</div>
    <div class="salutation">Dear Mr. John,</div>
    <p>Lorem Ipsum is simply dummy text of the printing and typesetting industry. Lorem Ipsum has been the industry's standard dummy text ever since the 1500s, when an unknown printer took a galley of type and scrambled it to make a type specimen book. It has survived not only five centuries, but also the leap into electronic typesetting, remaining essentially unchanged.</p>
    <p>The standard chunk of Lorem Ipsum used since the 1500s is reproduced below for those interested. Sections 1.10.32 and 1.10.33 from "de Finibus Bonorum et Malorum" by Cicero are also reproduced in their exact original form, accompanied by English versions from the 1914 translation by H. Rackham.</p>
    <p>Lorem Ipsum is simply dummy text of the printing and typesetting industry. Lorem Ipsum has been the industry's standard dummy text ever since the 1500s, when an unknown printer took a galley of type and scrambled it to make a type specimen book. It has survived not only five centuries, but also the leap into electronic typesetting, remaining essentially unchanged. It was popularised in the</p>
    <div class="signoff">Sincerely Your,</div>
    <div class="signature">your name</div>
    <div class="signer">Name Last Name<br>Company Name</div>
  </section>

  <div class="footer-details">
    <div class="company">Meridian Realty Group, LLC</div>
    <div>SUITE 102 STREET NAME, STATE, ZIP 2034, COUNTRY</div>
  </div>

  <footer class="contact-bar">
    <span class="contact-item"><svg viewBox="0 0 10 10"><path d="M2 1h2l1 2.5-1.2 1a5 5 0 0 0 2.7 2.7l1-1.2L10 7v2a1 1 0 0 1-1 1A8 8 0 0 1 1 2a1 1 0 0 1 1-1z"/></svg>(00) 01234 567 890</span>
    <span class="contact-item"><svg viewBox="0 0 10 10"><path d="M2 1h2l1 2.5-1.2 1a5 5 0 0 0 2.7 2.7l1-1.2L10 7v2a1 1 0 0 1-1 1A8 8 0 0 1 1 2a1 1 0 0 1 1-1z"/></svg>(00) 01234 567 891</span>
    <span class="contact-item"><svg viewBox="0 0 10 10"><path d="M0 2h10v6H0z M0 2l5 3.5L10 2" /></svg>hello@meridianrealty.com</span>
    <span class="contact-item"><svg viewBox="0 0 10 10"><circle cx="5" cy="5" r="4.5"/></svg>www.meridianrealtygroup.com</span>
  </footer>
</main>
</body>
</html>
```